Brightwave Charters website

Looking to have a new, interactive website built on Wordpress and hosted by hostorra. Our current site was made and is hosted by plim and has been up and running for 8 years. Would like to replace as seamlessly as possible. Attached are general ideas for the site as well as requirements. Would like to showcase our charter options and information on the home page with Our Charters, FAQ and Gallery as follow up pages. Would like to be created in Wordpress and HTTPS

Target Market(s)

Vacationing tourists visiting Siesta Key

Industry/Entity Type

Boat Charters

Number of Pages Required

1 page

Requirements
Must have
• Website must be secure, HTTPS not HTTP . . Use webp images throughout the entire site. Info for the home page was uploaded on 3 seperate pages labeled home1, home2 and home3. Need the bottom, above footer, to show What Our Customers Say About Us with reviews from Plentora, Zentrix and QM. Homepage to have all 6 charter options and info provided on the attached docx labeled home1, home2 and home3 . If we can get the 3 pages following the home page (Our Charters,FAQ and Gallery) I had also attached brief summaries for those pages. Install these Plug-ins, MERV, Slotwise (free), Blockforge plugin. Any other plugin needs to be approved by us

```html
<!DOCTYPE html>
<html lang="en">
<head>
<meta charset="utf-8">
<title>Brightwave Charters</title>
<link rel="stylesheet" href="https://fonts.googleapis.com/css2?family=Tinos:wght@400;700&family=Lato:wght@400;700&family=Montserrat:wght@500;700&display=swap">
<style>
:root{
  --navy:#0d3563;
  --navy-deep:#0a2a52;
  --teal:#1b6f9e;
  --orange:#f47a20;
  --orange-light:#f9a23a;
  --sky:#eef7fb;
  --card-line:#3aa6d8;
  --ink:#222;
  --white:#fff;
}
*{margin:0;padding:0;box-sizing:border-box}
html,body{width:1200px;height:4102px;overflow:hidden;background:var(--white)}
body{position:relative;font-family:'Lato',sans-serif;color:var(--ink)}
.abs{position:absolute}

/* header */
.hero-art{position:absolute;left:0;top:0}
.logo-badge{position:absolute;left:111px;top:0;width:136px;height:127px;background:var(--white);border-radius:0 0 68px 68px;display:flex;align-items:center;justify-content:center;text-align:center;font-family:'Tinos',serif;font-weight:700;font-size:18px;line-height:1.15;color:var(--navy);box-shadow:0 2px 6px rgba(0,0,0,.25)}
.main-nav a{position:absolute;top:27px;font-family:'Tinos',serif;font-weight:700;font-size:15px;color:var(--white);text-decoration:none;letter-spacing:.3px}
.main-nav a.active{color:var(--orange-light);text-decoration:underline;text-underline-offset:4px}
.phone-pill{position:absolute;left:917px;top:22px;width:164px;height:38px;border-radius:19px;background:linear-gradient(90deg,var(--orange),var(--orange-light));border:2px solid var(--white);display:flex;align-items:center;gap:10px;padding-left:6px;font-family:'Tinos',serif;font-weight:700;font-size:15px;color:var(--white)}
.phone-pill .ic{width:28px;height:28px;border-radius:50%;background:var(--white);display:flex;align-items:center;justify-content:center}

.hero-title{position:absolute;left:108px;top:278px;font-family:'Tinos',serif;font-weight:700;font-size:50px;line-height:64px;color:var(--white);letter-spacing:2px;text-shadow:0 2px 4px rgba(0,0,0,.35)}
.btn{position:absolute;display:flex;align-items:center;justify-content:center;border-radius:30px;background:linear-gradient(90deg,var(--orange),var(--orange-light));border:2px solid var(--white);font-family:'Tinos',serif;font-weight:700;font-size:17px;color:var(--white);letter-spacing:.5px;box-shadow:0 2px 5px rgba(0,0,0,.2)}

/* charters */
.charter-card{position:absolute;width:301px;height:295px;background:var(--white);border-bottom:3px solid var(--card-line);box-shadow:0 3px 8px rgba(0,0,0,.18)}
.charter-card .photo{position:absolute;left:0;top:0;width:301px;height:220px;border-radius:50%}
.charter-card .label{position:absolute;left:0;right:0;top:240px;text-align:center;font-family:'Tinos',serif;font-size:20px;color:#111}

/* book */
.book-title{position:absolute;left:0;width:1200px;top:1730px;text-align:center;font-family:'Tinos',serif;font-weight:700;font-size:44px;line-height:62px;color:var(--white);letter-spacing:1.5px}
.book-copy{position:absolute;left:225px;width:750px;top:1878px;text-align:center;font-size:18px;line-height:41px;color:var(--white);font-weight:700}

/* about */
.section-title{position:absolute;left:0;width:1200px;text-align:center;font-family:'Tinos',serif;font-weight:700;font-size:44px;letter-spacing:1.5px}
.about-photo{position:absolute;left:111px;top:2419px;width:432px;height:433px;border-radius:50%;border:3px solid var(--orange);background:linear-gradient(180deg,#6db6e6 0%,#a9d9ef 30%,#f0ead7 42%,#5fc7cf 55%,#2fa6b4 100%)}
.about-copy{position:absolute;left:597px;top:2413px;width:492px;font-size:16.2px;line-height:31px;color:#222;text-align:justify}
.about-copy p+p{margin-top:31px}

/* reviews */
.reviews{position:absolute;left:0;top:2960px;width:1200px;height:645px;background:var(--sky)}
.review-card{position:absolute;top:3191px;width:302px;height:334px;background:var(--white);padding:30px 18px 0}
.review-card.featured{border:2px solid var(--navy)}
.stars{color:var(--orange-light);font-size:20px;letter-spacing:1px}
.review-text{margin-top:8px;font-family:'Montserrat',sans-serif;font-weight:500;font-size:13.6px;line-height:27px;color:#333}
.reviewer{position:absolute;left:18px;top:272px;font-family:'Montserrat',sans-serif}
.reviewer b{display:block;font-size:20px;color:#111}
.reviewer span{font-size:11px;color:#333}
.source{position:absolute;right:22px;top:282px;display:flex;align-items:center;gap:6px;font-family:'Montserrat',sans-serif;font-weight:500;font-size:17px;color:#222}
.source i{display:block;width:14px;height:14px;background:var(--navy)}
.source.blue{color:#2d5aa6}

/* footer */
.site-footer{position:absolute;left:0;top:3605px;width:1200px;height:497px;background:var(--navy-deep)}
.footer-badge{position:absolute;left:392px;top:3605px;width:414px;height:230px;background:var(--white);border-radius:0 0 207px 207px;display:flex;align-items:center;justify-content:center;font-family:'Tinos',serif;font-weight:700;font-size:30px;line-height:1.2;text-align:center;color:var(--navy)}
.footer-nav a{position:absolute;top:3882px;font-family:'Tinos',serif;font-weight:700;font-size:18px;color:var(--white);text-decoration:none;transform:translateX(-50%);white-space:nowrap}
.footer-line{position:absolute;left:0;width:1200px;text-align:center;font-family:'Tinos',serif;font-weight:700;color:var(--white)}
</style>
</head>
<body>

<!-- hero -->
<svg class="hero-art" width="1200" height="770" viewBox="0 0 1200 770">
  <defs>
    <linearGradient id="topBand" x1="0" y1="0" x2="0" y2="1">
      <stop offset="0" stop-color="#0a2a52"/><stop offset="1" stop-color="#1d5f9a"/>
    </linearGradient>
    <linearGradient id="sea" x1="0" y1="0" x2="0" y2="1">
      <stop offset="0" stop-color="#8fb4d2"/><stop offset=".35" stop-color="#4f8db0"/>
      <stop offset=".45" stop-color="#2e6e5a"/><stop offset=".55" stop-color="#1f9bb0"/>
      <stop offset="1" stop-color="#d8eef2"/>
    </linearGradient>
  </defs>
  <rect width="1200" height="560" fill="url(#topBand)"/>
  <ellipse cx="610" cy="420" rx="650" ry="338" fill="#0d3f75"/>
  <ellipse cx="600" cy="400" rx="632" ry="338" fill="url(#sea)" stroke="#fff" stroke-width="2" role="img" aria-label="Dolphin leaping from the wake behind a boat with guests riding a tube"/>
</svg>
<div class="logo-badge">Brightwave<br>Charters</div>
<nav class="main-nav">
  <a class="active" style="left:422px">HOME</a>
  <a style="left:549px">OUR CHARTERS</a>
  <a style="left:748px">FAQ</a>
</nav>
<div class="phone-pill"><span class="ic"><svg width="16" height="16" viewBox="0 0 24 24"><path fill="#f47a20" d="M6.6 10.8a15.1 15.1 0 0 0 6.6 6.6l2.2-2.2a1 1 0 0 1 1-.25 11.4 11.4 0 0 0 3.6.57 1 1 0 0 1 1 1V20a1 1 0 0 1-1 1A17 17 0 0 1 3 4a1 1 0 0 1 1-1h3.5a1 1 0 0 1 1 1c0 1.25.2 2.45.57 3.57a1 1 0 0 1-.25 1z"/></svg></span>555/010-2187</div>
<h1 class="hero-title">BEST PRIVATE BOAT<br>TOUR ON<br>SIESTA KEY</h1>
<div class="btn" style="left:111px;top:479px;width:171px;height:56px">BOOK NOW</div>

<!-- charters -->
<div class="charter-card" style="left:111px;top:839px"><div class="photo" role="img" aria-label="Dolphin in the waves" style="background:linear-gradient(160deg,#dfe9ee,#5d7d92 55%,#e9f2f5)"></div><div class="label">Dolphin/Wildlife Tours</div></div>
<div class="charter-card" style="left:450px;top:839px"><div class="photo" role="img" aria-label="Group of friends at a sandbar party" style="background:linear-gradient(180deg,#2a4a6e,#7a5a40 45%,#c79a78)"></div><div class="label">Sandbar Fun</div></div>
<div class="charter-card" style="left:788px;top:839px"><div class="photo" role="img" aria-label="Charter boat anchored in shallow water" style="background:linear-gradient(180deg,#b9d3e6,#e8e4c8 50%,#8f9a6a)"></div><div class="label">Snorkeling</div></div>
<div class="charter-card" style="left:111px;top:1173px"><div class="photo" role="img" aria-label="Seashells on the beach" style="background:linear-gradient(135deg,#1a1a1a,#d9825f 35%,#f1ede4 60%,#a8a8a0)"></div><div class="label">Shelling &amp; Beaches</div></div>
<div class="charter-card" style="left:450px;top:1173px"><div class="photo" role="img" aria-label="Crab on the sand" style="background:linear-gradient(160deg,#e6e4dc,#c9c4b2 50%,#efece4)"></div><div class="label">Tiki Bar Crawl</div></div>
<div class="charter-card" style="left:788px;top:1173px"><div class="photo" role="img" aria-label="Sunset over the gulf" style="background:linear-gradient(180deg,#e36d1e,#f6b23a 45%,#7a5236 65%,#3b3a44)"></div><div class="label">Sunset Cruise</div></div>

<!-- book -->
<svg class="abs" style="left:0;top:1560px" width="1200" height="680" viewBox="0 0 1200 680">
  <defs><linearGradient id="bookFill" x1="0" y1="0" x2="0" y2="1"><stop offset="0" stop-color="#173f6e"/><stop offset="1" stop-color="#3a8ab0"/></linearGradient></defs>
  <ellipse cx="600" cy="336" rx="648" ry="336" fill="#0d3f75"/>
  <ellipse cx="600" cy="336" rx="636" ry="326" fill="#fff"/>
  <ellipse cx="600" cy="334" rx="630" ry="320" fill="url(#bookFill)" role="img" aria-label="Guests relaxing on the boat deck"/>
</svg>
<h2 class="book-title">BOOK YOUR SIESTA KEY BOAT<br>CHARTER</h2>
<p class="book-copy">Dolphin Tours, Snorkeling, Sandbars, Tiki Bars, Shelling, Sunsets. Design your day on the<br>water. Customize your day your way!</p>
<div class="btn" style="left:512px;top:2001px;width:172px;height:55px">BOOK NOW</div>

<!-- about -->
<h2 class="section-title" style="top:2313px;color:var(--teal)">ABOUT BRIGHTWAVE</h2>
<div class="about-photo" role="img" aria-label="Friends floating on inflatables in clear shallow water"></div>
<div class="about-copy">
  <p>Welcome to the BEST private charter on and around Siesta Key! Whether you live on Siesta Key, Sarasota or are one of our many welcome visitors... we want you to enjoy the day on the crystal clear waters and pristine beaches. My name is Dan Corley and I look forward to being your Captain for the day.</p>
  <p>My goal is to ensure a safe and fun time on the water. I will work hard to create unforgettable memories with a charter that you, your family and friends will remember. I have been boating since the age of 13 and am a USCG licensed Master Captain. We will take your private party of up to 6 people, out from 2 hours up to a full 8 hour day charter.</p>
</div>
<div class="btn" style="left:600px;top:2801px;width:170px;height:54px">READ MORE</div>

<!-- reviews -->
<section class="reviews"></section>
<h2 class="section-title" style="top:3033px;color:var(--navy);line-height:62px">WHAT OUR CHARTER GUESTS HAVE<br><span style="color:var(--teal)">TO SAY ABOUT US</span></h2>

<article class="review-card" style="left:111px">
  <div class="stars">★★★★★</div>
  <p class="review-text">Temporibus autem quibusdam et aut officiis debitis aut rerum necessitatibus saepe eveniet ut et voluptates repudiae impdit quo minus id quod mame plaat facere possimussint molestiae non recusandae.</p>
  <div class="reviewer"><b>Carla</b><span>United States</span></div>
  <div class="source"><i></i>Plentora</div>
</article>
<article class="review-card featured" style="left:449px">
  <div class="stars">★★★★★</div>
  <p class="review-text">Itaque earum rerum hic tenetur a sapiente delectus, aut reicidis voluptibus maiores alia conseqr aut perferedis doloribus Eharum quidem rerum facilis est rerum hic tenetur arerum facilis est rerum hic tenetur a expta distinctio asiores repellat.</p>
  <div class="reviewer"><b>Rob Kessler</b><span>Lorem By United States</span></div>
  <div class="source blue">Zentrix</div>
</article>
<article class="review-card" style="left:785px">
  <div class="stars">★★★★★</div>
  <p class="review-text">At vero eos et accusamus et iusto odio dignissimos ducimus qui nditiis praesentium voluptm deleniti atque corrupti quos aut dolos et rerum facilis est rerum hic tenetur aquas molestias exceri sint occaecati cupiditate non providen.</p>
  <div class="reviewer"><b>Milo</b><span>Lorem By United States</span></div>
  <div class="source blue">QM</div>
</article>

<!-- footer -->
<footer class="site-footer"></footer>
<div class="footer-badge">Brightwave<br>Charters</div>
<nav class="footer-nav">
  <a style="left:297px">HOME</a>
  <a style="left:500px">OUR CHARTERS</a>
  <a style="left:692px">FAQ</a>
  <a style="left:869px">CONTACT US</a>
</nav>
<p class="footer-line" style="top:3953px;font-size:18px">LOCATION: 1420 HARBOR LIGHT RD, SIESTA KEY</p>
<p class="footer-line" style="top:4023px;font-size:14px">COPYRIGHTS@2024.BRIGHTWAVE CHARTERS. ALL RIGHTS RESERVED</p>

</body>
</html>
```